TLK Electricial Contracting Services

Hi guys, after a design for my small electrical company, have logo design files to be incorporated into the layout, the basic concept is electrical contracting services for residential, commercial, industrial & data services, image is clean clear and strong,

Card format is to have a nice clean logo on front,with maybe the Residential – commercial – industrial - data, followed with licensed & insured, followed by contact details on backside of the card.

Target Market(s)

Residential, commercial, industrial sectors.

Industry/Entity Type

Electrical

Contact Information for Business Card

TLK logo,
Residential – commercial – industrial - data
REC: 61307
Email: tlk@vornamail.net.au
Phone: 0487 352 019

Requirements
Must have
• Clean & strong design.
Nice to have
• If possible, I would like the logo colours inverted so the text is orange and the background is black on the front of the card, then the backside of the card be the reverse colour
Should not have
• No Sparks, lightning bolts,

```html
<!DOCTYPE html>
<html lang="en">
<head>
<meta charset="utf-8">
<title>TLK Electrical Contracting Services – Business Card</title>
<link rel="stylesheet" href="https://fonts.googleapis.com/css2?family=Exo+2:wght@700;800&family=Open+Sans:wght@400;600&display=swap">
<style>
  :root {
    --orange: #f47b20;
    --black: #0c0c0c;
    --stage: #e6e6e6;
    --card-w: 500px;
    --card-h: 290px;
  }
  * { box-sizing: border-box; margin: 0; padding: 0; }
  html, body {
    width: 1200px;
    height: 873px;
    overflow: hidden;
    background: var(--stage);
  }
  .stage {
    position: relative;
    width: 1200px;
    height: 873px;
    display: flex;
    align-items: center;
    justify-content: center;
    gap: 60px;
  }
  .card {
    position: relative;
    width: var(--card-w);
    height: var(--card-h);
    overflow: hidden;
    box-shadow: 0 6px 18px rgba(0,0,0,0.18);
  }

  /* Back: contact side */
  .card--back { background: var(--orange); color: var(--black); }
  .skyline-band {
    position: absolute;
    left: 0; top: 0; bottom: 0;
    width: 58px;
    background: linear-gradient(90deg, var(--black) 70%, #2a2a2a 100%);
  }
  .back-brand {
    position: absolute;
    left: 100px;
    top: 30px;
  }
  .brand-mark {
    font-family: "Exo 2", sans-serif;
    font-weight: 800;
    line-height: 0.9;
    letter-spacing: -1px;
  }
  .back-brand .brand-mark { font-size: 56px; }
  .brand-name {
    font-family: "Exo 2", sans-serif;
    font-weight: 800;
    font-size: 12px;
    letter-spacing: 0.2px;
    white-space: nowrap;
  }
  .licence {
    font-family: "Open Sans", sans-serif;
    font-size: 8px;
    text-align: right;
    margin-top: 1px;
  }
  .contact-list {
    position: absolute;
    left: 100px;
    top: 140px;
    list-style: none;
    font-family: "Open Sans", sans-serif;
    font-size: 17px;
  }
  .contact-item {
    display: flex;
    align-items: center;
    gap: 14px;
    height: 44px;
    white-space: nowrap;
  }
  .contact-icon { width: 32px; height: 32px; flex: none; }

  /* Front: logo side */
  .card--front { background: var(--black); color: var(--orange); }
  .front-brand {
    position: absolute;
    left: 50%;
    top: 50%;
    transform: translate(-50%, -50%);
    text-align: left;
  }
  .front-brand .brand-mark { font-size: 120px; }
  .front-brand .brand-name { font-size: 24px; margin-top: 6px; }
  .sectors {
    font-family: "Open Sans", sans-serif;
    font-weight: 600;
    font-size: 11px;
    letter-spacing: 0.6px;
    text-transform: uppercase;
    margin-top: 10px;
    white-space: nowrap;
  }
</style>
</head>
<body>
<main class="stage">

  <section class="card card--back" aria-label="Business card back">
    <div class="skyline-band" role="img" aria-label="Black city skyline silhouette with houses and trees along the card edge"></div>

    <div class="back-brand">
      <div class="brand-mark">TLK</div>
      <div class="brand-name">Tobin Lake Electrical</div>
      <div class="licence">REC: 61307</div>
    </div>

    <ul class="contact-list">
      <li class="contact-item">
        <svg class="contact-icon" viewBox="0 0 32 32" aria-hidden="true">
          <circle cx="16" cy="16" r="13" fill="none" stroke="currentColor" stroke-width="3"/>
          <path d="M10 16.5l4 4 8-9" fill="none" stroke="currentColor" stroke-width="3" stroke-linecap="round" stroke-linejoin="round"/>
        </svg>
        <span>Licensed &amp; Insured</span>
      </li>
      <li class="contact-item">
        <svg class="contact-icon" viewBox="0 0 32 32" aria-hidden="true">
          <path d="M4 11c0-4 5-6 12-6s12 2 12 6v2h-6v-3h-12v3H4z" fill="currentColor"/>
          <path d="M8 15h16l3 12H5z" fill="currentColor"/>
          <circle cx="16" cy="21" r="3" fill="var(--orange)"/>
        </svg>
        <span>0487 352 019</span>
      </li>
      <li class="contact-item">
        <svg class="contact-icon" viewBox="0 0 32 32" aria-hidden="true">
          <rect x="2" y="7" width="28" height="19" fill="currentColor"/>
          <path d="M2 7l14 11 14-11" fill="none" stroke="var(--orange)" stroke-width="1.6"/>
        </svg>
        <span>tlk@vornamail.net.au</span>
      </li>
    </ul>
  </section>

  <section class="card card--front" aria-label="Business card front">
    <div class="front-brand">
      <div class="brand-mark">TLK</div>
      <div class="brand-name">Tobin Lake Electrical</div>
      <div class="sectors">Residential – Commercial – Industrial – Data</div>
    </div>
  </section>

</main>
</body>
</html>
```